Business Cards for IT Consulting Company (Managed Service Provider)

I am looking to have some business cards printed and would like some designs. We are an IT Consulting company based in Vancouver BC. I would like a nice clean and modern look to the cards. I have uploaded all the versions of my logo so parts can be used as needed. Here is a snippit from our website homepage:

Quillbrook Networks Ltd. is an IT Solutions Partner located in Vancouver BC, Canada. We offer IT solutions and support to customers in the greater Vancouver Area. With expertise in Microsoft platforms, as well as Linux and Mac OSX and over 12 years experience in the IT industry, Quillbrook Networks is dedicated to offering our clients top quality service and products. We take pride in the solutions we offer our customers. The greatest compliment a client can give us is to recommend our services.

Quillbrook Networks Ltd. offers a wide range of IT services from onsite service to remote support and managed service solutions. This allows clients to choose the support path that best suits their company’s needs. Supporting many different sized companies from small to enterprise level over the past 12 years Quillbrook Networks has the experience and expertise needed to ensure things run smoothly. Allowing our clients to focus on doing business.

Revolutionizing the way IT services are delivered.

Quillbrook Networks is dedicated to providing our clients with IT solutions that work and grow with them for years to come. This philosophy helps save money in the long run instead of replacing equipment constantly. Far too often IT solutions are not well thought out and while possibly solving the problem at hand, require replacement due to growth or quality within a very short time frame. Quillbrook Networks takes pride in providing solutions that will last and be able to accommodate growth without the need for replacement.

Industry/Entity Type

Information Technology

Contact Information for Business Card

Quillbrook Networks Ltd.
(Employee Name)
Eml: (Employees Email Address)
Web: quillbrook.me
Ph: 604-555-0148

Font styles to use
Serif
Sans Serif

Requirements
Must have
• The Company logo and company colors.
Nice to have
• - Our tag line: "Revolutionizing IT Services" or "Revolutionizing the way IT services are delivered."
• - Also I really like the idea of nature and technology together blending which is sort of where my logo came from so integrating that somehow onto the business cards would be great.

```html
<!DOCTYPE html>
<html lang="en">
<head>
<meta charset="utf-8">
<title>Quillbrook Networks Ltd. — Business Card</title>
<link rel="stylesheet" href="https://fonts.googleapis.com/css2?family=Source+Sans+3:wght@400;600;700&display=swap">
<style>
  :root {
    --brand-blue: #19a9e1;
    --brand-grey: #5a5b5e;
    --text-grey: #56575a;
    --paper: #ffffff;
    --backdrop: #e9eaec;
  }
  * { box-sizing: border-box; margin: 0; padding: 0; }
  html, body {
    width: 1105px;
    height: 1200px;
    overflow: hidden;
    background: var(--backdrop);
    font-family: "Source Sans 3", sans-serif;
  }
  .card {
    position: absolute;
    left: 196px;
    width: 720px;
    height: 412px;
    overflow: hidden;
  }
  .card--front { top: 146px; background: var(--paper); }
  .card--back  { top: 602px; background: var(--brand-blue); }

  .brand {
    position: absolute;
    left: 48px;
    top: 72px;
    display: flex;
    align-items: center;
    gap: 14px;
  }
  .brand__mark {
    width: 26px;
    height: 26px;
    background: var(--brand-blue);
  }
  .brand__name {
    font-size: 36px;
    font-weight: 600;
    color: var(--brand-blue);
    line-height: 1;
  }

  .contact {
    position: absolute;
    left: 141px;
    top: 160px;
    color: var(--text-grey);
  }
  .contact__name {
    font-size: 30px;
    font-weight: 600;
    color: var(--brand-blue);
    line-height: 1;
    margin-bottom: 14px;
  }
  .contact__address {
    font-size: 19px;
    line-height: 27px;
    margin-bottom: 8px;
  }
  .contact__list { list-style: none; }
  .contact__item {
    display: flex;
    align-items: center;
    font-size: 19px;
    line-height: 27.5px;
  }
  .contact__icon {
    width: 16px;
    height: 16px;
    margin-right: 13px;
    fill: var(--brand-blue);
    flex: none;
  }

  .front-band {
    position: absolute;
    left: 0;
    bottom: 0;
    width: 720px;
    height: 24px;
  }

  .back-pattern {
    position: absolute;
    inset: 0;
    background: linear-gradient(135deg, #1aa9e1 0%, #22afe4 50%, #16a3dc 100%);
  }
  .back-mark {
    position: absolute;
    left: 305px;
    top: 158px;
    width: 110px;
    height: 110px;
    border: 4px solid var(--paper);
    border-radius: 50%;
  }
  .tagline {
    position: absolute;
    left: 0;
    right: 0;
    top: 326px;
    text-align: center;
    font-size: 19px;
    font-weight: 600;
    color: var(--paper);
  }
</style>
</head>
<body>
  <section class="card card--front" aria-label="Business card front">
    <div class="brand">
      <span class="brand__mark" aria-hidden="true"></span>
      <span class="brand__name">Quillbrook Networks Ltd.</span>
    </div>

    <div class="contact">
      <p class="contact__name">Maren Holloway</p>
      <p class="contact__address">2140 Alder Crescent<br>Vancouver, BC V5K 0A1</p>
      <ul class="contact__list">
        <li class="contact__item">
          <svg class="contact__icon" viewBox="0 0 16 16" aria-hidden="true"><path d="M3.2 1.2l2.4 0 1.2 3.3-1.6 1.2c.8 1.8 2.3 3.3 4.1 4.1l1.2-1.6 3.3 1.2v2.4c0 .9-.8 1.6-1.7 1.5C6.6 12.8 3.2 9.4 2.7 2.9c-.1-.9.6-1.7 1.5-1.7z"/></svg>
          604-555-0148
        </li>
        <li class="contact__item">
          <svg class="contact__icon" viewBox="0 0 16 16" aria-hidden="true"><path d="M1 3.5h14v9H1z M1.6 4.2L8 9l6.4-4.8" fill="none" stroke="#19a9e1" stroke-width="1.4"/><path d="M1 3.5h14L8 8.6z"/></svg>
          mholloway@quillbrook.me
        </li>
        <li class="contact__item">
          <svg class="contact__icon" viewBox="0 0 16 16" aria-hidden="true"><circle cx="8" cy="8" r="7"/><path d="M4 5c1.5 0 2 1 3 1s.5 2-1 2.5S5 11 6 12.5M10 2.5c-.5 1.5.5 2 1.5 2.5s.5 2.5 2 2.5" fill="none" stroke="#fff" stroke-width="1.2"/></svg>
          www.quillbrook.me
        </li>
      </ul>
    </div>

    <svg class="front-band" viewBox="0 0 720 24" aria-hidden="true">
      <path d="M0 9h521l7-6h17l7 6v15H0z" fill="var(--brand-blue)"/>
      <path d="M556 9l7-6h17l7 6h133v15H556z" fill="var(--brand-grey)"/>
    </svg>
  </section>

  <section class="card card--back" aria-label="Business card back">
    <div class="back-pattern" role="img" aria-label="Faint repeating geometric pattern in lighter blue"></div>
    <span class="back-mark" aria-hidden="true"></span>
    <p class="tagline">Revolutionizing IT Services</p>
  </section>
</body>
</html>
```